New web design for a service provider in the medical field

We are looking for a new design for our website. We are a company that repairs and sells medical endoscopes. Our customers include doctors and hospitals. Our current website can be found at https://lumavex.de/en/lumavex-english.
We need a new web design (without programming) for the following 3 pages:
-Startpage https://lumavex.de/en/lumavex-english/
-Used endoscopes https://lumavex.de/en/used-endoscopes/
-Purchase https://lumavex.de/en/purchase/
The design should be modern and stylish.
The blue color of the logo should be reflected on the page, but not too intrusive.
I have uploaded the images from the header. If more images are needed, let me know and I will upload them.

Target Market(s)
Doctors and hospitals

```html
<!DOCTYPE html>
<html lang="en">
<head>
<meta charset="utf-8">
<title>Lumavex – Endoscope Repair &amp; Sale</title>
<link href="https://fonts.googleapis.com/css2?family=Poppins:wght@400;500;600&display=swap" rel="stylesheet">
<style>
:root{
  --blue:#29a8e0;
  --navy:#263f50;
  --ink:#2b3a45;
  --muted:#5d6b75;
  --pale:#f4f7f9;
  --line:#c9d6e0;
  --white:#ffffff;
}
*{box-sizing:border-box;margin:0;padding:0}
html,body{width:1200px;height:4777px;overflow:hidden}
body{font-family:'Poppins',sans-serif;color:var(--ink);background:var(--white);position:relative}
.abs{position:absolute}
a{color:inherit;text-decoration:none}
.btn{position:absolute;background:var(--blue);color:var(--white);font-size:13px;border-radius:20px;padding:7px 20px;white-space:nowrap;transform:translateX(-50%)}
.center{text-align:center}

/* header */
.topbar{position:absolute;left:352px;top:0;width:848px;height:37px;background:var(--navy);clip-path:polygon(30px 0,100% 0,100% 100%,0 100%)}
.topbar span{position:absolute;top:10px;color:var(--white);font-size:11.5px}
.lang-on{position:absolute;top:4px;width:30px;height:30px;border-radius:50%;background:var(--blue);color:var(--white);font-size:11.5px;text-align:center;line-height:30px}
.brand{position:absolute;left:66px;top:30px;font-size:22px;font-weight:600;color:var(--navy);display:flex;align-items:center;gap:8px}
.brand i{width:12px;height:12px;border-radius:50%;background:var(--blue);display:block}
.nav a{position:absolute;top:58px;font-size:12.5px;color:var(--navy);text-transform:uppercase}
.nav a.active{color:var(--blue)}

/* hero */
.hero{position:absolute;left:0;top:96px;width:1200px;height:500px;background:linear-gradient(115deg,#c9d0d6 0%,#9ea8b1 35%,#4c555d 60%,#b7c0c7 100%)}
.hero h1{position:absolute;left:0;top:115px;width:1200px;text-align:center;color:var(--white);font-size:38px;font-weight:500;line-height:1.35}
.hero .btn{top:270px;left:600px}
.wave{position:absolute;left:0;width:1200px}

.intro h2{position:absolute;top:652px;width:1200px;text-align:center;font-size:25px;font-weight:600;color:var(--navy)}
.intro p{position:absolute;left:370px;top:695px;width:460px;text-align:center;font-size:12.5px;line-height:22px;color:var(--muted)}

.about h2{position:absolute;left:61px;top:985px;width:600px;font-size:26px;font-weight:600;line-height:38px;color:var(--navy)}
.about p{position:absolute;left:61px;width:595px;font-size:12.5px;line-height:22px;color:var(--muted)}
.photo-circle{position:absolute;left:770px;top:955px;width:357px;height:357px;border-radius:50%;background:radial-gradient(circle at 45% 40%,#e9eef2 0%,#aeb8c0 60%,#6e7a84 100%)}

.brands{position:absolute;left:0;top:1395px;width:1200px;height:400px;background:var(--pale)}
.brands h2{position:absolute;left:61px;top:160px;width:640px;font-size:26px;font-weight:600;line-height:38px;color:var(--navy)}
.bubble{position:absolute;width:148px;height:148px;border-radius:50%;color:var(--white);font-size:19px;font-weight:600;display:flex;align-items:center;justify-content:center}

.services{position:absolute;left:0;top:1796px;width:1200px;height:467px;background:var(--navy);color:var(--white)}
.service{position:absolute;top:60px;width:330px;text-align:center;transform:translateX(-50%)}
.service .icon{width:100px;height:100px;margin:0 auto;border-radius:50%;background:var(--white);display:flex;align-items:center;justify-content:center}
.service .icon.hot{background:var(--blue);box-shadow:0 0 0 4px rgba(41,168,224,.35)}
.service h3{font-size:17px;font-weight:500;margin-top:28px}
.service h4{font-size:13px;font-weight:400;color:var(--blue);margin-top:6px}
.service p{font-size:12.5px;line-height:22px;margin-top:12px;color:#e4ebf0;height:112px}
.service .btn{position:relative;transform:none;display:inline-block;margin-top:18px}

.faulty .img{position:absolute;left:352px;top:2345px;width:492px;height:160px;background:linear-gradient(90deg,#ffffff 0%,#d3d8dc 40%,#2a2f34 80%,#5a6168 100%);border-radius:80px}
.faulty h2{position:absolute;top:2525px;width:1200px;text-align:center;font-size:26px;font-weight:600;color:var(--navy)}
.faulty p{position:absolute;width:1200px;text-align:center}

.outcome{position:absolute;left:0;top:2783px;width:1200px;height:556px;background:var(--pale)}
.outcome h2{position:absolute;top:50px;width:1200px;text-align:center;font-size:26px;font-weight:600;color:var(--navy)}
.card{position:absolute;background:var(--white);border:1.5px solid var(--line);border-radius:4px}
.feature{width:524px;height:116px}
.feature svg{position:absolute;left:32px;top:28px}
.feature h3{position:absolute;left:152px;top:30px;font-size:16px;font-weight:500;color:var(--blue)}
.feature p{position:absolute;left:152px;top:58px;width:350px;font-size:12.5px;line-height:22px;color:var(--muted)}

.decision h2{position:absolute;top:3420px;width:1200px;text-align:center;font-size:26px;font-weight:600;color:var(--navy)}
.benefit{width:339px;height:265px;text-align:center}
.benefit svg{margin-top:26px}
.benefit h3{font-size:16px;font-weight:500;color:var(--blue);margin-top:14px}
.benefit p{font-size:12.5px;line-height:22px;color:var(--muted);margin:12px 26px 0}

.help{position:absolute;left:0;top:4127px;width:1200px;height:303px;background:var(--navy);color:var(--white);text-align:center}
.help h2{position:absolute;top:70px;width:1200px;font-size:26px;font-weight:500}
.help p{position:absolute;left:315px;top:130px;width:570px;font-size:12.5px;line-height:22px}
.help .btn{top:213px;left:600px}

.footer h4{position:absolute;font-size:13px;font-weight:500;color:var(--navy)}
.footer a{position:absolute;font-size:11px;color:var(--navy);text-transform:uppercase}
.footer .contact{position:absolute;font-size:12px;color:var(--navy);display:flex;gap:10px;align-items:center}
.social{position:absolute;top:4663px;width:31px;height:31px;border-radius:50%;border:1.5px solid var(--navy)}
.social.filled{background:var(--blue);border-color:var(--blue)}
.legalbar{position:absolute;left:0;top:4740px;width:1200px;height:37px;background:var(--blue);color:var(--white);font-size:11.5px;text-align:center;line-height:37px}
</style>
</head>
<body>

<!-- header -->
<div class="topbar">
  <span style="left:160px">Pick-Up Order</span>
  <span style="left:272px">About Us</span>
  <span style="left:434px">✉&nbsp; info@lumavex.de</span>
  <span style="left:630px">☎&nbsp; +49 4100 555 210-0</span>
  <span style="left:726px;left:725px;left:726px;left:728px;left:728px;left:728px;left:728px;left:728px;left:728px;left:728px;left:728px;left:728px;left:728px;left:728px;left:728px;left:728px;left:728px;left:728px;left:728px;left:728px;left:728px;left:728px;left:728px;left:728px;left:733px">DE</span>
  <div class="lang-on" style="left:751px">EN</div>
</div>
<div class="brand"><i></i>Lumavex</div>
<nav class="nav">
  <a class="active" style="left:300px">Home</a>
  <a style="left:371px">Endoscope Repair</a>
  <a style="left:531px">Used Endoscopes</a>
  <a style="left:689px">Endoscopy Systems</a>
  <a style="left:864px">Endoscopy Accessories</a>
  <a style="left:1068px">Purchase</a>
</nav>

<!-- hero -->
<section class="hero" role="img" aria-label="Photo of a flexible medical endoscope lying on a light surface">
  <h1>Put Your Endoscope In Reliable<br>Hands!</h1>
  <a class="btn">Contact Us</a>
</section>
<svg class="wave" style="top:520px" width="1200" height="100" viewBox="0 0 1200 100" preserveAspectRatio="none">
  <path d="M0 45 C250 110 450 10 700 45 C900 72 1050 30 1200 50 L1200 100 L0 100Z" fill="#e9eef2"/>
  <path d="M0 60 C260 120 480 30 720 62 C920 88 1060 50 1200 70 L1200 100 L0 100Z" fill="#ffffff"/>
</svg>

<!-- intro -->
<section class="intro">
  <svg class="wave" style="top:760px" width="1200" height="160" viewBox="0 0 1200 160" preserveAspectRatio="none">
    <path d="M0 0 L1200 0 L1200 90 C950 150 700 60 450 100 C250 130 120 150 0 120Z" fill="#f4f7f9"/>
  </svg>
  <div class="abs" style="left:0;top:596px;width:1200px;height:164px;background:var(--pale)"></div>
  <h2>Your Future - Our Service</h2>
  <p>Lumavex GmbH is specialised in the repair and sale of Orvane, Pentrix and Fujora flexible medical endoscopes. As a service-oriented company, we are at your side with our knowledge and skills!</p>
</section>

<!-- about -->
<section class="about">
  <h2>Endoscope repairs and second hand endoscopes from Lumavex – cause the outcome matters!</h2>
  <p style="top:1103px">Lumavex is a privileged partner for the start-up facility or optimisation of existing healthcare facilities, doctor's offices and hospitals. The quality and reliability of our products and our offered service are our best advertisement!</p>
  <p style="top:1180px">As a result of optimised processes and highly qualified specialists in our company, we can work very quickly and with high quality for your benefit of least possible restrictions in your doctor's office or in your hospital.</p>
  <div class="photo-circle" role="img" aria-label="Round photo of an endoscope control body"></div>
</section>

<!-- brands -->
<section class="brands">
  <h2>You'll get advises manufacturer independent and with absolute transparency!</h2>
  <div class="bubble" style="left:766px;top:52px;background:var(--blue)">Orvane</div>
  <div class="bubble" style="left:991px;top:52px;background:var(--blue)">Pentrix</div>
  <div class="bubble" style="left:881px;top:199px;background:var(--navy)">Fujora</div>
</section>

<!-- services -->
<section class="services">
  <div class="service" style="left:258px">
    <div class="icon"><svg width="54" height="54" viewBox="0 0 54 54" fill="none" stroke="#263f50" stroke-width="2.2"><circle cx="24" cy="24" r="9"/><path d="M24 6v6M24 36v6M6 24h6M36 24h6M11 11l4 4M33 33l4 4M11 37l4-4M37 11l-4 4"/><path d="M32 32l14 14" stroke="#29a8e0" stroke-width="3"/></svg></div>
    <h3>Repair</h3><h4>Endoscope repair service</h4>
    <p>Manufacturer-independent we repair and maintain endoscopes, individual components (e.g. processors or light sources), accessories and peripherals of the manufacturers Orvane, Pentrix and Fujora.</p>
    <a class="btn">Repair request</a>
  </div>
  <div class="service" style="left:599px">
    <div class="icon hot"><svg width="54" height="54" viewBox="0 0 54 54" fill="none" stroke="#fff" stroke-width="2.2"><circle cx="27" cy="27" r="18"/><circle cx="27" cy="27" r="11"/><path d="M31 22c-1-2-7-2-7 1s7 2 7 5-6 3-7 1M27 18v3M27 33v3"/></svg></div>
    <h3>Sale</h3><h4>Used endoscopes</h4>
    <p>Our regular stock includes refurbished gastroscopes, coloscopes, bronchoscopes, cystoscopes and duodenoscopes from the well-known manufacturers Orvane, Pentrix and Fujora.</p>
    <a class="btn">Purchase request</a>
  </div>
  <div class="service" style="left:966px">
    <div class="icon"><svg width="54" height="54" viewBox="0 0 54 54" fill="none" stroke="#263f50" stroke-width="2.2"><circle cx="27" cy="27" r="14"/><path d="M13 27h28M27 13c-6 8-6 20 0 28M27 13c6 8 6 20 0 28"/><rect x="4" y="6" width="10" height="7" stroke="#29a8e0"/><rect x="40" y="41" width="10" height="7" stroke="#29a8e0"/></svg></div>
    <h3>Purchase</h3><h4>Used endoscopes</h4>
    <p>We are very interested in buying your old endoscopes – even defective and dismantled! We offer fair conditions! Please contact us for a purchase offer!</p>
    <a class="btn">Sell device</a>
  </div>
</section>

<!-- faulty -->
<section class="faulty">
  <div class="img" role="img" aria-label="Photo of a flexible endoscope with its insertion tube"></div>
  <h2>Faulty Endoscope?</h2>
  <p style="top:2572px;font-size:13px;color:var(--muted)">We ensure quick and smooth repairs!</p>
  <p style="top:2610px;font-size:16px;font-weight:500;color:var(--navy)">Simple place a</p>
  <a class="btn" style="top:2670px;left:600px">Pick Up Order</a>
</section>

<!-- outcome -->
<section class="outcome">
  <h2>Cause the Outcome Matters!</h2>
  <div class="card feature" style="left:61px;top:113px">
    <svg width="60" height="60" viewBox="0 0 60 60" fill="none" stroke="#263f50" stroke-width="2"><rect x="6" y="28" width="34" height="26"/><path d="M23 35v12M17 41h12" stroke="#29a8e0"/><circle cx="44" cy="12" r="5"/><path d="M38 26c0-6 12-6 12 0v28"/></svg>
    <h3>One company for everyone</h3><p>We are a service provider for doctors and hospitals!</p>
  </div>
  <div class="card feature" style="left:616px;top:113px">
    <svg width="60" height="60" viewBox="0 0 60 60" fill="none" stroke="#263f50" stroke-width="2"><circle cx="30" cy="32" r="6"/><circle cx="16" cy="36" r="5"/><circle cx="44" cy="36" r="5"/><path d="M20 54c0-12 20-12 20 0M6 54c0-9 14-10 16-6M54 54c0-9-14-10-16-6"/><path d="M30 6l3 6 6 1-5 4 1 6-5-3-5 3 1-6-5-4 6-1z" stroke="#29a8e0"/></svg>
    <h3>Experience charactersises us</h3><p>Our team has many years of experience in the business field!</p>
  </div>
  <div class="card feature" style="left:61px;top:255px">
    <svg width="60" height="60" viewBox="0 0 60 60" fill="none" stroke="#263f50" stroke-width="2"><rect x="10" y="6" width="34" height="46"/><path d="M17 16h20M17 24h20M17 32h14"/><path d="M44 52c-8-6-10-9-8-12 2-2 5-1 8 2 3-3 6-4 8-2 2 3 0 6-8 12z" stroke="#29a8e0"/></svg>
    <h3>The product is close to our hearts</h3><p>We repair and sell second hand, flexible endoscopes!</p>
  </div>
  <div class="card feature" style="left:616px;top:255px">
    <svg width="60" height="60" viewBox="0 0 60 60" fill="none" stroke="#263f50" stroke-width="2"><rect x="22" y="6" width="30" height="40"/><path d="M28 16l3 3 5-6M28 28l3 3 5-6M40 18h8M40 30h8"/><circle cx="16" cy="42" r="8" stroke="#29a8e0"/><circle cx="16" cy="42" r="3" stroke="#29a8e0"/></svg>
    <h3>Guaranteed service</h3><p>You receive a six-month warranty on all repairs!</p>
  </div>
  <div class="card feature" style="left:61px;top:397px">
    <svg width="60" height="60" viewBox="0 0 60 60" fill="none" stroke="#263f50" stroke-width="2"><circle cx="20" cy="14" r="7" stroke="#29a8e0"/><circle cx="42" cy="20" r="7" stroke="#29a8e0"/><path d="M4 46h12l10 4h14l14-10M16 40h14c4 0 4 6 0 6h-8"/></svg>
    <h3>Quality not quantity</h3><p>Reliability and durability instead of inferior replacements!</p>
  </div>
  <div class="card feature" style="left:616px;top:397px">
    <svg width="60" height="60" viewBox="0 0 60 60" fill="none" stroke="#263f50" stroke-width="2"><circle cx="24" cy="22" r="10"/><circle cx="24" cy="22" r="4" stroke="#29a8e0"/><path d="M24 6v4M24 34v4M8 22h4M36 22h4"/><rect x="6" y="44" width="46" height="10" rx="5"/><circle cx="14" cy="49" r="2"/><circle cx="24" cy="49" r="2"/><circle cx="34" cy="49" r="2"/><circle cx="44" cy="49" r="2"/></svg>
    <h3>Services for everyone</h3><p>Our service includes the manufacturers Orvane, Pentrix and Fujora!</p>
  </div>
</section>

<!-- decision -->
<section class="decision">
  <h2>Lumavex GmbH, your decision for your future</h2>
  <div class="card benefit" style="left:61px;top:3489px">
    <svg width="64" height="70" viewBox="0 0 64 70" fill="none" stroke="#263f50" stroke-width="2.4"><circle cx="32" cy="40" r="26"/><circle cx="32" cy="40" r="12" stroke="#29a8e0"/><path d="M32 34v6l4 3M26 4h12M32 4v10" stroke="#29a8e0"/></svg>
    <h3>Fast repairs</h3><p>Keep potential disruptions in your doctor's office or in your hospital at minimum as a result of optimized processes and highly qualified specialists in our company</p>
  </div>
  <div class="card benefit" style="left:430px;top:3489px">
    <svg width="70" height="64" viewBox="0 0 70 64" fill="none" stroke="#263f50" stroke-width="2.4"><path d="M4 32L35 6l31 26M12 26v34h46V26"/><rect x="28" y="40" width="14" height="20" stroke="#29a8e0"/></svg>
    <h3>On-site service</h3><p>We will gladly pay you a visit to to carry out analysis and repairs on site. Due to our many years of experience – it doesn't get any faster (whigleithin a 250 km range)</p>
  </div>
  <div class="card benefit" style="left:801px;top:3489px">
    <svg width="64" height="64" viewBox="0 0 64 64" fill="none" stroke="#263f50" stroke-width="2.2"><rect x="24" y="4" width="34" height="52"/><path d="M32 16l3 3 5-6M32 30l3 3 5-6M46 16h6M46 30h6"/><circle cx="16" cy="38" r="9" stroke="#29a8e0"/><circle cx="22" cy="54" r="6" stroke="#29a8e0"/></svg>
    <h3>Without a maintenance contract</h3><p>No subscription or other maintenance contract, but one-time and sustainable repair work</p>
  </div>
  <div class="card benefit" style="left:61px;top:3779px">
    <svg width="64" height="64" viewBox="0 0 64 64" fill="none" stroke="#263f50" stroke-width="2.2"><path d="M6 58V26M20 58V14M44 58V14M58 58V26M4 58h56"/><circle cx="32" cy="36" r="10" stroke="#29a8e0"/><path d="M27 41l10-10M28 32h1M36 40h1" stroke="#29a8e0"/></svg>
    <h3>Highly cost efficient</h3><p>Benefit from our first class recommendations and implementation by our experienced staff. Our goals is to find the best solutions together with you at the best lowest price point.</p>
  </div>
  <div class="card benefit" style="left:430px;top:3779px">
    <svg width="64" height="64" viewBox="0 0 64 64" fill="none" stroke="#263f50" stroke-width="2.2"><path d="M22 8h20l-6 10h-8z"/><path d="M28 18c-16 8-16 30 4 30s20-22 4-30"/><path d="M35 28c-2-2-6-1-6 1s6 2 6 5-5 3-7 1M32 24v3M32 37v3" stroke="#29a8e0"/><path d="M4 52h12l10 6h18l16-10"/></svg>
    <h3>Loan equipment service</h3><p>Use our service of high-quality loan devices during the downtime of your defective endoscope (limited to stock)</p>
  </div>
  <div class="card benefit" style="left:801px;top:3779px">
    <svg width="64" height="64" viewBox="0 0 64 64" fill="none" stroke="#263f50" stroke-width="2.2"><circle cx="32" cy="24" r="18"/><circle cx="32" cy="24" r="11" stroke="#29a8e0"/><path d="M32 17l2 5 5 0-4 3 2 5-5-3-5 3 2-5-4-3 5 0z" stroke="#29a8e0"/><path d="M22 40l-6 18 8-4 4 8 4-12M42 40l6 18-8-4-4 8-4-12"/></svg>
    <h3>First class service</h3><p>Our clients always come first!</p>
  </div>
</section>

<!-- help -->
<section class="help">
  <h2>How can we help you?</h2>
  <p>Lorem Ipsum is simply dummy text of the printing and typesetting industry. Lorem Ipsum has been the industry's standard dummy text ever since the 1500s, when an unknown printer</p>
  <a class="btn">We Will Contact You</a>
</section>

<!-- footer -->
<footer class="footer">
  <div class="brand" style="left:74px;top:4556px;font-size:24px"><i></i>Lumavex</div>
  <span class="social filled" style="left:61px"></span>
  <span class="social" style="left:108px"></span>
  <span class="social" style="left:155px"></span>
  <span class="social" style="left:203px"></span>

  <h4 style="left:497px;top:4540px">Company</h4>
  <a style="left:500px;top:4576px;color:var(--blue)">Home</a>
  <a style="left:497px;top:4610px">Endoscope Repair</a>
  <a style="left:497px;top:4646px">Used Endoscopes</a>
  <a style="left:497px;top:4684px">Endoscopy Systems</a>
  <a style="left:653px;top:4568px">Endoscopy Accessories</a>
  <a style="left:651px;top:4602px">Purchase</a>

  <h4 style="left:946px;top:4540px">Legal</h4>
  <div class="contact" style="left:946px;top:4583px"><svg width="20" height="14" viewBox="0 0 20 14" fill="none" stroke="#29a8e0" stroke-width="1.5"><rect x="1" y="1" width="18" height="12"/><path d="M1 1l9 7 9-7"/></svg>info@lumavex.de</div>
  <div class="contact" style="left:946px;top:4625px"><svg width="18" height="18" viewBox="0 0 18 18" fill="none" stroke="#29a8e0" stroke-width="1.5"><path d="M4 1l3 4-2 2c1 3 3 5 6 6l2-2 4 3-2 3C8 17 1 10 1 3z"/></svg>+49 4100 555 210-0</div>
</footer>
<div class="legalbar">2022© Lumavex. All right reserved.</div>

</body>
</html>
```